BMR Going Cashless

Hello,
We are a medical office looking to get a flyer created to promote to our patients we will be going "Cashless." Our tagline will be "Cash-Less is Stress-Less"

"Starting in July, to offer you the fastest and most convenient service, we are transitioning to a cashless system. You can now enjoy faster checkout times and greater security with card and contactless payments. More info to come."

I've added two other flyers as sample designs we've used.

Please include logo, addresses, website, phone number

Files to include jpeg, png, pdf (under 5mb), Facebook and Instagram sizing.

Thank you,
Lowen

```html
<!DOCTYPE html>
<html lang="en">
<head>
<meta charset="utf-8">
<title>BMR Going Cashless</title>
<link rel="stylesheet" href="https://fonts.googleapis.com/css2?family=Poppins:wght@400;500;600;700;800&family=Bebas+Neue&display=swap">
<style>
:root{
  --orange:#f07b3f;
  --orange-deep:#e8662a;
  --teal:#52c3a0;
  --ink:#2b2b2b;
  --white:#ffffff;
  --stage:#b5b5b5;
  --shadow-text:#d8d8d8;
  --photo-light:#ecd3bf;
  --photo-mid:#d9b497;
}
*{box-sizing:border-box;margin:0;padding:0}
html,body{width:1200px;height:2400px;overflow:hidden}
body{background:var(--stage);position:relative;font-family:"Poppins",sans-serif;color:var(--white)}
.flyer{position:absolute;background:var(--white);overflow:hidden}
.flyer--square{left:158px;top:149px;width:883px;height:883px}
.flyer--portrait{left:263px;top:1099px;width:675px;height:1200px}
.abs{position:absolute}
.dark-panel{position:absolute;left:0;right:0;bottom:0;background:var(--ink)}
.photo-slot{position:absolute;background:linear-gradient(180deg,var(--photo-light) 0%,var(--photo-mid) 100%)}
.headline-top{color:var(--orange);text-align:center;line-height:1;white-space:nowrap}
.headline-sub{font-family:"Poppins",sans-serif;font-weight:800;color:var(--teal);text-align:center;line-height:1;white-space:nowrap;text-shadow:4px 6px 0 var(--shadow-text)}
.tab-start{background:var(--orange);color:var(--white);font-weight:500;letter-spacing:.28em;display:flex;align-items:center;justify-content:center;border-radius:0 8px 8px 0}
.month{font-family:"Bebas Neue",sans-serif;color:var(--teal);line-height:.8}
.offer-title{font-weight:700;line-height:1}
.offer-body{font-weight:500;color:var(--white)}
.teal-band{background:linear-gradient(90deg,var(--teal) 0%,var(--teal) 55%,rgba(82,195,160,.55) 80%,rgba(82,195,160,0) 100%)}
.band-text{font-weight:600;color:var(--white)}
.badge{position:absolute}
.badge-text{position:absolute;inset:0;display:flex;align-items:center;justify-content:center;text-align:center;font-weight:800;line-height:.95}
.badge-text span{display:block}
.badge-top{color:var(--ink)}
.badge-rest{color:var(--white)}
.brand{display:flex;align-items:center;gap:12px}
.brand-dot{border-radius:50%;background:var(--teal)}
.brand-name{font-weight:700;color:var(--orange);letter-spacing:.02em}
.office-name{color:var(--orange);font-weight:700;display:flex;align-items:center;gap:6px;white-space:nowrap}
.office-addr{font-weight:400;color:var(--white);white-space:nowrap}
.phone{font-weight:700;color:var(--white);display:flex;align-items:center;gap:10px;white-space:nowrap}
.web-bar{background:var(--orange);display:flex;align-items:center;justify-content:center;letter-spacing:.16em;color:var(--white);white-space:nowrap}
.web-bar b{font-weight:700;color:var(--ink)}
</style>
</head>
<body>

<section class="flyer flyer--square" aria-label="Cashless announcement, square format">
  <div class="dark-panel" style="top:380px"></div>
  <div class="photo-slot" role="img" aria-label="Photo: hand holding a bank card toward a card reader"
       style="left:0;top:240px;width:883px;height:580px;clip-path:polygon(0% 6%,100% 6%,100% 78%,92% 66%,72% 38%,0% 30%)"></div>

  <h1 class="headline-top abs" style="left:0;right:0;top:22px;font-family:'Poppins',sans-serif;font-weight:800;font-size:112px;letter-spacing:-1px">CASH-LESS</h1>
  <p class="headline-sub abs" style="left:0;right:0;top:130px;font-size:92px;letter-spacing:-1px">IS STRESS-LESS</p>

  <div class="tab-start abs" style="left:0;top:416px;width:282px;height:44px;font-size:24px">STARTING IN</div>
  <p class="month abs" style="left:54px;top:485px;font-size:128px">JULY</p>
  <p class="offer-title abs" style="left:252px;top:477px;font-size:27px">TO OFFER YOU</p>
  <p class="offer-body abs" style="left:252px;top:510px;width:360px;font-size:20px;line-height:24px">the fastest and most convenient service, we are transitioning to a cashless system</p>

  <div class="teal-band abs" style="left:0;top:599px;width:883px;height:64px"></div>
  <p class="band-text abs" style="left:52px;top:606px;font-size:20px;line-height:25px">You can now enjoy faster checkout times and<br>greater security with card and contactless payments.</p>

  <div class="badge" style="left:609px;top:488px;width:186px;height:186px">
    <svg width="186" height="186" viewBox="0 0 186 186" aria-hidden="true">
      <g fill="var(--orange-deep)">
        <circle cx="93" cy="93" r="82"/>
        <circle cx="93" cy="12" r="12"/><circle cx="124" cy="18" r="12"/><circle cx="150" cy="36" r="12"/><circle cx="168" cy="62" r="12"/>
        <circle cx="174" cy="93" r="12"/><circle cx="168" cy="124" r="12"/><circle cx="150" cy="150" r="12"/><circle cx="124" cy="168" r="12"/>
        <circle cx="93" cy="174" r="12"/><circle cx="62" cy="168" r="12"/><circle cx="36" cy="150" r="12"/><circle cx="18" cy="124" r="12"/>
        <circle cx="12" cy="93" r="12"/><circle cx="18" cy="62" r="12"/><circle cx="36" cy="36" r="12"/><circle cx="62" cy="18" r="12"/>
      </g>
      <circle cx="93" cy="93" r="76" fill="none" stroke="var(--white)" stroke-width="2"/>
    </svg>
    <p class="badge-text" style="font-size:33px"><span><span class="badge-top">MORE</span><span class="badge-rest">INFO TO</span><span class="badge-rest">COME</span></span></p>
  </div>

  <div class="brand abs" style="left:37px;top:712px">
    <span class="brand-dot" style="width:42px;height:42px"></span>
    <span class="brand-name" style="font-size:52px;line-height:1">BMR</span>
  </div>
  <div class="web-bar abs" style="left:0;top:801px;width:329px;height:38px;font-size:19px;border-radius:0 6px 6px 0">www.<b>bmrcare</b>.com</div>

  <div class="abs" style="left:349px;top:697px">
    <p class="office-name" style="font-size:21px"><svg width="14" height="20" viewBox="0 0 14 20" aria-hidden="true"><path d="M7 0a7 7 0 0 0-7 7c0 5 7 13 7 13s7-8 7-13a7 7 0 0 0-7-7zm0 10a3 3 0 1 1 0-6 3 3 0 0 1 0 6z" fill="var(--teal)"/></svg>Northgate Office</p>
    <p class="office-addr" style="font-size:14.5px;line-height:18px;margin-top:6px">218 Elmwood Park<br>Dr.Suite140 Northgate, MD20911</p>
  </div>
  <div class="abs" style="left:606px;top:699px">
    <p class="office-name" style="font-size:21px"><svg width="14" height="20" viewBox="0 0 14 20" aria-hidden="true"><path d="M7 0a7 7 0 0 0-7 7c0 5 7 13 7 13s7-8 7-13a7 7 0 0 0-7-7zm0 10a3 3 0 1 1 0-6 3 3 0 0 1 0 6z" fill="var(--teal)"/></svg>Riverside Office</p>
    <p class="office-addr" style="font-size:14.5px;line-height:18px;margin-top:6px">45MeadowLane<br>Riverside,WV25990</p>
  </div>
  <div class="abs" style="left:606px;top:776px">
    <p class="office-name" style="font-size:21px"><svg width="14" height="20" viewBox="0 0 14 20" aria-hidden="true"><path d="M7 0a7 7 0 0 0-7 7c0 5 7 13 7 13s7-8 7-13a7 7 0 0 0-7-7zm0 10a3 3 0 1 1 0-6 3 3 0 0 1 0 6z" fill="var(--teal)"/></svg>Hillcrest Office</p>
    <p class="office-addr" style="font-size:14.5px;line-height:18px;margin-top:6px">7710 Birchwood<br>Blvd.Suite 305 Hillcrest, MD20988</p>
  </div>

  <p class="phone abs" style="left:349px;top:804px;font-size:27px">
    <svg width="24" height="24" viewBox="0 0 24 24" aria-hidden="true"><circle cx="12" cy="12" r="12" fill="var(--teal)"/><path d="M8.5 6.5c.6-.4 1.2-.2 1.5.3l1 1.8c.3.5.1 1-.3 1.3l-.7.5c.5 1.3 1.6 2.5 2.9 3.1l.6-.7c.4-.4.9-.5 1.3-.2l1.8 1c.5.3.7.9.3 1.5-.8 1.2-2 1.6-3.3 1.1-3-1.1-5.3-3.5-6.3-6.5-.4-1.3.1-2.5 1.2-3.2z" fill="var(--white)"/></svg>
    (555)210-4477
  </p>
</section>

<section class="flyer flyer--portrait" aria-label="Cashless announcement, portrait format">
  <div class="dark-panel" style="top:540px"></div>
  <div class="photo-slot" role="img" aria-label="Photo: hand holding a bank card toward a card reader"
       style="left:0;top:405px;width:675px;height:420px;clip-path:polygon(0% 4%,100% 4%,100% 78%,86% 60%,66% 46%,0% 40%)"></div>

  <div class="brand abs" style="left:0;right:0;top:62px;justify-content:center">
    <span class="brand-dot" style="width:52px;height:52px"></span>
    <span class="brand-name" style="font-size:66px;line-height:1">BMR</span>
  </div>

  <h1 class="headline-top abs" style="left:0;right:0;top:181px;font-family:'Bebas Neue',sans-serif;font-size:176px;letter-spacing:1px">CASH-LESS</h1>
  <p class="headline-sub abs" style="left:0;right:0;top:321px;font-size:74px;letter-spacing:-1px">IS STRESS-LESS</p>

  <div class="tab-start abs" style="left:0;top:608px;width:293px;height:42px;font-size:24px">STARTING IN</div>
  <p class="month abs" style="left:63px;top:680px;font-size:126px">JULY</p>
  <p class="offer-title abs" style="left:262px;top:669px;font-size:27px">TO OFFER YOU</p>
  <p class="offer-body abs" style="left:262px;top:702px;width:380px;font-size:20px;line-height:24px">the fastest and most convenient service, we are transitioning to a cashless system</p>

  <div class="teal-band abs" style="left:175px;top:801px;width:500px;height:145px"></div>
  <p class="band-text abs" style="left:225px;top:812px;font-size:23px;line-height:28px">You can now enjoy faster<br>checkout times and greater<br>security with card<br>and contactless payments.</p>

  <div class="badge" style="left:40px;top:789px;width:168px;height:168px">
    <svg width="168" height="168" viewBox="0 0 186 186" aria-hidden="true">
      <g fill="var(--orange-deep)">
        <circle cx="93" cy="93" r="82"/>
        <circle cx="93" cy="12" r="12"/><circle cx="124" cy="18" r="12"/><circle cx="150" cy="36" r="12"/><circle cx="168" cy="62" r="12"/>
        <circle cx="174" cy="93" r="12"/><circle cx="168" cy="124" r="12"/><circle cx="150" cy="150" r="12"/><circle cx="124" cy="168" r="12"/>
        <circle cx="93" cy="174" r="12"/><circle cx="62" cy="168" r="12"/><circle cx="36" cy="150" r="12"/><circle cx="18" cy="124" r="12"/>
        <circle cx="12" cy="93" r="12"/><circle cx="18" cy="62" r="12"/><circle cx="36" cy="36" r="12"/><circle cx="62" cy="18" r="12"/>
      </g>
      <circle cx="93" cy="93" r="76" fill="none" stroke="var(--white)" stroke-width="2"/>
    </svg>
    <p class="badge-text" style="font-size:29px"><span><span class="badge-top">MORE</span><span class="badge-rest">INFO TO</span><span class="badge-rest">COME</span></span></p>
  </div>

  <div class="abs" style="left:40px;top:1000px">
    <p class="office-name" style="font-size:18px"><svg width="12" height="18" viewBox="0 0 14 20" aria-hidden="true"><path d="M7 0a7 7 0 0 0-7 7c0 5 7 13 7 13s7-8 7-13a7 7 0 0 0-7-7zm0 10a3 3 0 1 1 0-6 3 3 0 0 1 0 6z" fill="var(--teal)"/></svg>Northgate Office</p>
    <p class="office-addr" style="font-size:12.5px;line-height:16px;margin-top:6px">218 Elmwood Park<br>Dr.Suite140 Northgate, MD20911</p>
  </div>
  <div class="abs" style="left:243px;top:1000px">
    <p class="office-name" style="font-size:18px"><svg width="12" height="18" viewBox="0 0 14 20" aria-hidden="true"><path d="M7 0a7 7 0 0 0-7 7c0 5 7 13 7 13s7-8 7-13a7 7 0 0 0-7-7zm0 10a3 3 0 1 1 0-6 3 3 0 0 1 0 6z" fill="var(--teal)"/></svg>Riverside Office</p>
    <p class="office-addr" style="font-size:12.5px;line-height:16px;margin-top:6px">45MeadowLane<br>Riverside,WV25990</p>
  </div>
  <div class="abs" style="left:447px;top:1000px">
    <p class="office-name" style="font-size:18px"><svg width="12" height="18" viewBox="0 0 14 20" aria-hidden="true"><path d="M7 0a7 7 0 0 0-7 7c0 5 7 13 7 13s7-8 7-13a7 7 0 0 0-7-7zm0 10a3 3 0 1 1 0-6 3 3 0 0 1 0 6z" fill="var(--teal)"/></svg>Hillcrest Office</p>
    <p class="office-addr" style="font-size:12.5px;line-height:16px;margin-top:6px">7710 Birchwood<br>Blvd.Suite 305 Hillcrest, MD20988</p>
  </div>

  <p class="phone abs" style="left:35px;top:1102px;font-size:32px">
    <svg width="30" height="30" viewBox="0 0 24 24" aria-hidden="true"><circle cx="12" cy="12" r="12" fill="var(--teal)"/><path d="M8.5 6.5c.6-.4 1.2-.2 1.5.3l1 1.8c.3.5.1 1-.3 1.3l-.7.5c.5 1.3 1.6 2.5 2.9 3.1l.6-.7c.4-.4.9-.5 1.3-.2l1.8 1c.5.3.7.9.3 1.5-.8 1.2-2 1.6-3.3 1.1-3-1.1-5.3-3.5-6.3-6.5-.4-1.3.1-2.5 1.2-3.2z" fill="var(--white)"/></svg>
    (555)210-4477
  </p>
  <div class="web-bar abs" style="left:332px;top:1106px;width:343px;height:35px;font-size:19px;border-radius:6px 0 0 6px">www.<b>bmrcare</b>.com</div>
</section>

</body>
</html>
```